Kestrel Bathrooms Facelift. Moving the business in to the next professional level.

I'm currently revamping my bathroom renovation business. Part of this revamp includes our marketing strategy to better position ourselves as a professional business. As the name suggests, we primarily do bathroom renovations of all shapes, sizes and budgets. I'd like a business card design that is simple, yet displays our company as sophisticated.
What I'd like is to have a card that incorporates the following elements;
- Orange set as the primary colour and Charcoal/Grey as a complement colour. The card can also include white and/or black.
- I'd like a hexagon pattern within the charcoal/grey (In gloss perhaps to break it up a bit)
- I only want the Kestrel Bathrooms logo on the front of the card
- Back of the card would include contact details
- The bottom edges of the card would be rounded off
- I've attached the company name. I'd like to keep kestrel as it is. Bathrooms can be modified

```html
<!DOCTYPE html>
<html lang="en">
<head>
<meta charset="utf-8">
<title>Kestrel Bathrooms – Business Card</title>
<link rel="stylesheet" href="https://fonts.googleapis.com/css2?family=Quicksand:wght@300;500;600&display=swap">
<style>
  :root {
    --page-bg: #e6e6e4;
    --charcoal: #2b2c2e;
    --charcoal-deep: #1c1d1f;
    --charcoal-gloss: #46484b;
    --orange: #f07a1a;
    --card-white: #ffffff;
    --panel-shade: #f1f1f1;
    --ink-dark: #2b2c2e;
    --ink-light: #ffffff;
    --ink-muted: #d6d6d6;
    --card-shadow: 0 14px 30px rgba(0, 0, 0, 0.22);
  }
  * { box-sizing: border-box; margin: 0; padding: 0; }
  html, body {
    width: 1200px;
    height: 900px;
    overflow: hidden;
    background: var(--page-bg);
    font-family: "Quicksand", sans-serif;
  }
  .canvas { position: relative; width: 1200px; height: 900px; }
  .card {
    position: absolute;
    left: 300px;
    width: 600px;
    height: 340px;
    border-radius: 38px;
    overflow: hidden;
    box-shadow: var(--card-shadow);
  }
  .card--front { top: 80px; background: var(--charcoal); }
  .card--back {
    top: 480px;
    background: linear-gradient(160deg, var(--card-white) 0%, var(--panel-shade) 100%);
  }
  .hex-gloss {
    position: absolute;
    left: 0;
    top: 0;
    width: 300px;
    height: 340px;
    background: linear-gradient(135deg, var(--charcoal-gloss) 0%, var(--charcoal) 45%, var(--charcoal-deep) 100%);
  }
  .card__shapes { position: absolute; inset: 0; width: 600px; height: 340px; }
  .holder { position: absolute; left: 40px; top: 36px; color: var(--ink-light); }
  .holder__name { font-size: 21px; font-weight: 600; letter-spacing: 0.01em; }
  .holder__role { font-size: 14px; font-weight: 500; color: var(--ink-muted); margin-top: 2px; }
  .contacts {
    position: absolute;
    left: 40px;
    bottom: 58px;
    list-style: none;
    color: var(--ink-light);
    font-size: 14px;
    font-weight: 500;
  }
  .contacts__item { display: flex; align-items: center; gap: 10px; margin-top: 6px; }
  .contacts__icon { width: 18px; height: 18px; flex: none; }
  .wordmark {
    position: absolute;
    color: var(--ink-dark);
    font-weight: 300;
    text-align: right;
    line-height: 1;
  }
  .wordmark__name { display: block; }
  .wordmark__sub { display: block; letter-spacing: 0.22em; font-weight: 500; color: var(--orange); }
  .card--front .wordmark { left: 320px; top: 128px; width: 230px; }
  .card--front .wordmark__name { font-size: 62px; letter-spacing: 0.02em; }
  .card--front .wordmark__sub { font-size: 15px; margin-top: 8px; }
  .card--back .wordmark { left: 150px; top: 112px; width: 300px; }
  .card--back .wordmark__name { font-size: 80px; letter-spacing: 0.02em; }
  .card--back .wordmark__sub { font-size: 19px; margin-top: 10px; }
  .accent-band {
    position: absolute;
    left: 0;
    bottom: 0;
    width: 600px;
    height: 14px;
    background: var(--orange);
  }
</style>
</head>
<body>
<main class="canvas">

  <section class="card card--front" aria-label="Business card front">
    <div class="hex-gloss" role="img" aria-label="Glossy charcoal hexagon pattern"></div>
    <svg class="card__shapes" viewBox="0 0 600 340" aria-hidden="true">
      <path fill="var(--orange)" d="M250 340 L250 150 Q250 20 380 20 L600 20 L600 340 Z"/>
      <path fill="var(--card-white)" d="M285 340 L285 140 Q285 30 395 30 L600 30 L600 340 Z"/>
    </svg>

    <div class="holder">
      <p class="holder__name">Dorian Valcourt</p>
      <p class="holder__role">Director</p>
    </div>

    <ul class="contacts">
      <li class="contacts__item">
        <svg class="contacts__icon" viewBox="0 0 18 18" aria-hidden="true">
          <circle cx="9" cy="9" r="9" fill="var(--orange)"/>
          <path d="M6 4.5 L7.6 4.5 L8.3 6.8 L7.3 7.6 Q8 9.6 10.4 10.7 L11.2 9.7 L13.5 10.4 L13.5 12 Q12.5 13.5 10.5 13 Q5.5 11.5 4.8 6.5 Q4.8 5 6 4.5 Z" fill="var(--ink-light)"/>
        </svg>
        <span>012 555 0147</span>
      </li>
      <li class="contacts__item">
        <svg class="contacts__icon" viewBox="0 0 18 18" aria-hidden="true">
          <circle cx="9" cy="9" r="9" fill="var(--orange)"/>
          <rect x="6" y="3.5" width="6" height="11" rx="1.2" fill="var(--ink-light)"/>
          <rect x="7" y="5" width="4" height="6.5" fill="var(--orange)"/>
        </svg>
        <span>012 555 0148</span>
      </li>
      <li class="contacts__item">
        <svg class="contacts__icon" viewBox="0 0 18 18" aria-hidden="true">
          <circle cx="9" cy="9" r="9" fill="var(--orange)"/>
          <rect x="4" y="5.5" width="10" height="7" rx="1" fill="var(--ink-light)"/>
          <path d="M4.5 6 L9 9.5 L13.5 6" fill="none" stroke="var(--orange)" stroke-width="1"/>
        </svg>
        <span>hello@kestrelmail.com</span>
      </li>
    </ul>

    <div class="wordmark">
      <span class="wordmark__name">kestrel</span>
      <span class="wordmark__sub">BATHROOMS</span>
    </div>
  </section>

  <section class="card card--back" aria-label="Business card back">
    <div class="wordmark">
      <span class="wordmark__name">kestrel</span>
      <span class="wordmark__sub">BATHROOMS</span>
    </div>
    <div class="accent-band"></div>
  </section>

</main>
</body>
</html>
```